New letter head for Air Conditioning business

We need a new professional letter head design to suit our new re-branded air conditioning business. Our new logo is attached

```html
<!DOCTYPE html>
<html lang="en">
<head>
<meta charset="utf-8">
<title>Norvane Letterhead</title>
<link href="https://fonts.googleapis.com/css2?family=Montserrat:wght@700&family=Open+Sans:wght@400&display=swap" rel="stylesheet">
<style>
  :root {
    --paper: #ffffff;
    --ink: #3c3c3c;
    --brand-grey: #5a5a5a;
    --accent-orange: #ef7b57;
    --accent-green: #86c47b;
    --divider: #c9c9c9;
  }
  html, body {
    margin: 0;
    padding: 0;
    overflow: hidden;
    background: var(--paper);
  }
  .letterhead {
    position: relative;
    width: 863px;
    height: 1200px;
    background: var(--paper);
    overflow: hidden;
  }
  .brand {
    position: absolute;
    left: 60px;
    top: 92px;
    display: flex;
    align-items: center;
    gap: 16px;
  }
  .brand-dot {
    width: 26px;
    height: 26px;
    border-radius: 50%;
    background: var(--accent-orange);
  }
  .brand-name {
    font-family: "Montserrat", sans-serif;
    font-weight: 700;
    font-size: 46px;
    letter-spacing: 3px;
    color: var(--brand-grey);
  }
  .header-divider {
    position: absolute;
    left: 420px;
    top: 30px;
    width: 1px;
    height: 180px;
    background: var(--divider);
  }
  .contact {
    position: absolute;
    left: 438px;
    top: 30px;
    margin: 0;
    padding: 0;
    list-style: none;
    font-family: "Open Sans", sans-serif;
    font-size: 17px;
    color: var(--ink);
  }
  .contact-item {
    display: flex;
    align-items: center;
    gap: 14px;
    height: 46px;
  }
  .contact-company { padding-left: 0; }
  .contact-icon {
    width: 18px;
    height: 18px;
    flex: none;
  }
  .footer-band {
    position: absolute;
    left: 0;
    bottom: 0;
    width: 863px;
    height: 40px;
  }
</style>
</head>
<body>
  <div class="letterhead">
    <div class="brand">
      <span class="brand-dot"></span>
      <span class="brand-name">NORVANE</span>
    </div>

    <div class="header-divider"></div>

    <ul class="contact">
      <li class="contact-item contact-company">Norvane Air Conditioning &amp; Refrigeration Address</li>
      <li class="contact-item">
        <svg class="contact-icon" viewBox="0 0 24 24" aria-hidden="true">
          <path fill="#ef7b57" d="M6.6 10.8a15.1 15.1 0 0 0 6.6 6.6l2.2-2.2c.3-.3.7-.4 1-.2 1.1.4 2.3.6 3.6.6.6 0 1 .4 1 1V20c0 .6-.4 1-1 1C10.6 21 3 13.4 3 4c0-.6.4-1 1-1h3.5c.6 0 1 .4 1 1 0 1.3.2 2.5.6 3.6.1.3 0 .7-.2 1z"/>
        </svg>
        +60 1000 2000
      </li>
      <li class="contact-item">
        <svg class="contact-icon" viewBox="0 0 24 24" aria-hidden="true">
          <rect x="3" y="5" width="18" height="14" rx="1.5" fill="none" stroke="#ef7b57" stroke-width="2"/>
          <path d="M3.5 6l8.5 7 8.5-7" fill="none" stroke="#ef7b57" stroke-width="2"/>
        </svg>
        info@norvaneaircon .com
      </li>
      <li class="contact-item">
        <svg class="contact-icon" viewBox="0 0 24 24" aria-hidden="true">
          <circle cx="12" cy="12" r="9" fill="none" stroke="#ef7b57" stroke-width="2"/>
          <ellipse cx="12" cy="12" rx="4" ry="9" fill="none" stroke="#ef7b57" stroke-width="2"/>
          <path d="M3 12h18" stroke="#ef7b57" stroke-width="2"/>
        </svg>
        www.norvaneaircon .com
      </li>
    </ul>

    <svg class="footer-band" viewBox="0 0 863 40" preserveAspectRatio="none" aria-hidden="true">
      <polygon points="0,0 505,0 480,40 0,40" fill="#ef7b57"/>
      <polygon points="505,0 863,0 863,40 480,40" fill="#86c47b"/>
    </svg>
  </div>
</body>
</html>
```